Veltrane Group Business Card Design

The CEO is looking for a new trendy look for his business card.
You can stay with current branding or come up with something new/creative. It can be 3D, including Medical Office buildings. You can use our logo in a variety of colors. Please include name, title, company name, company website, email address, cell number

Target Market(s)

Real Estate Development and Construction

Industry/Entity Type

Health care real estate

Contact Information for Business Card

Rohesh Kamdar, CEO M-604.781.2249 E-roheshkamdar@veltrane.com Address:4180 Lindqvist Ave, Tampa, FL 33482 www.veltrane.com

Font styles to use
Other font styles liked:
• Be creative

Requirements
Must have
• Creative, trendy look
Nice to have
• Please go to our website to get a feel- www. veltrane.com
Should not have
• small fonts

```html
<!DOCTYPE html>
<html lang="en">
<head>
<meta charset="utf-8">
<title>Veltrane Group Business Card</title>
<link href="https://fonts.googleapis.com/css2?family=Montserrat:wght@400;700;800&display=swap" rel="stylesheet">
<style>
  :root {
    --bg: #d0d5d5;
    --paper: #f1f1ef;
    --brand-red: #b31e2a;
    --accent-red: #d8232e;
    --ink: #3a3a3a;
  }
  * { box-sizing: border-box; margin: 0; padding: 0; }
  html, body { width: 1200px; height: 881px; overflow: hidden; }
  body {
    background: var(--bg);
    font-family: "Montserrat", sans-serif;
    position: relative;
  }
  .card {
    position: absolute;
    top: 297px;
    width: 500px;
    height: 286px;
    background: var(--paper);
    border-bottom: 5px solid var(--accent-red);
    box-shadow: 0 14px 30px rgba(0,0,0,0.18);
  }
  .card--front { left: 70px; }
  .card--back { left: 630px; display: flex; align-items: center; justify-content: center; }

  .holder {
    position: absolute;
    top: 58px;
    left: 0;
    width: 100%;
    text-align: center;
  }
  .holder__name {
    color: var(--brand-red);
    font-weight: 700;
    font-size: 24px;
    letter-spacing: 0.5px;
    text-transform: uppercase;
  }
  .holder__title {
    color: var(--ink);
    font-size: 14px;
    margin-top: 2px;
  }
  .details {
    position: absolute;
    top: 150px;
    left: 0;
    width: 100%;
    display: flex;
    justify-content: center;
    align-items: stretch;
    gap: 16px;
    color: var(--ink);
    font-size: 13px;
  }
  .address { text-align: right; line-height: 1.5; padding-top: 4px; }
  .divider { width: 1.5px; background: var(--accent-red); }
  .contacts { list-style: none; line-height: 1.65; }
  .contacts li { display: flex; align-items: center; gap: 7px; }
  .contacts svg { width: 11px; height: 11px; flex: none; }

  .wordmark {
    display: flex;
    align-items: center;
    gap: 14px;
    color: var(--brand-red);
    font-weight: 800;
    font-size: 46px;
    letter-spacing: -1px;
  }
  .wordmark__square { width: 22px; height: 22px; background: var(--brand-red); }
</style>
</head>
<body>
  <section class="card card--front">
    <div class="holder">
      <h1 class="holder__name">Rohesh Kamdar</h1>
      <p class="holder__title">CEO</p>
    </div>
    <div class="details">
      <address class="address" style="font-style:normal">4180 Lindqvist Ave<br>Tampa, FL 33482</address>
      <span class="divider"></span>
      <ul class="contacts">
        <li>
          <svg viewBox="0 0 12 12"><rect x="3" y="0.5" width="6" height="11" rx="1" fill="none" stroke="#d8232e" stroke-width="1.2"/><circle cx="6" cy="9.5" r="0.7" fill="#d8232e"/></svg>
          604.781.2249
        </li>
        <li>
          <svg viewBox="0 0 12 12"><rect x="0.5" y="2.5" width="11" height="7" fill="#d8232e"/><path d="M0.5 2.5 L6 6.5 L11.5 2.5" fill="none" stroke="#f1f1ef" stroke-width="0.9"/></svg>
          roheshkamdar@veltrane.com
        </li>
        <li>
          <svg viewBox="0 0 12 12"><circle cx="6" cy="6" r="5.5" fill="#d8232e"/><path d="M0.5 6 H11.5 M6 0.5 C3 3 3 9 6 11.5 M6 0.5 C9 3 9 9 6 11.5" fill="none" stroke="#f1f1ef" stroke-width="0.7"/></svg>
          www.veltrane.com
        </li>
      </ul>
    </div>
  </section>

  <section class="card card--back">
    <div class="wordmark">
      <span class="wordmark__square"></span>
      <span class="wordmark__name">Veltrane Group</span>
    </div>
  </section>
</body>
</html>
```